Lumavento business card

We need a modern business card - With our 4 colors - See web: www.lumavento.dk

I have attached logo and som old business Cards we have - Lets Make the new ones shine...:-) -

Industry/Entity Type

Business

Requirements
Must have
• the logo with lumavento only,

```html
<!DOCTYPE html>
<html lang="da">
<head>
<meta charset="utf-8">
<title>Lumavento visitkort</title>
<link href="https://fonts.googleapis.com/css2?family=Source+Sans+3:wght@400;600&display=swap" rel="stylesheet">
<style>
  :root {
    --backdrop: #000000;
    --card: #f7fafa;
    --card-back: #f6f7f9;
    --lime: #a3c73a;
    --lime-faint: #e3edcf;
    --ink: #111111;
    --ink-soft: #3a3a3a;
    --divider: #e4e8e6;
    --ghost: #eef2f0;
  }
  * { margin: 0; padding: 0; box-sizing: border-box; }
  html, body { width: 1200px; height: 900px; overflow: hidden; background: var(--backdrop); }
  body { position: relative; font-family: "Source Sans 3", sans-serif; color: var(--ink); }

  .card { position: absolute; top: 271px; width: 457px; height: 281px; border-radius: 14px; }
  .card--front { left: 137px; background: var(--card); }
  .card--back { left: 626px; background: var(--card-back); }

  .brand { position: absolute; left: 12px; top: 118px; width: 205px; text-align: center; }
  .brand__mark { display: inline-block; width: 10px; height: 10px; border-radius: 50%; background: var(--lime); margin-right: 8px; vertical-align: 2px; }
  .brand__name { font-size: 17px; font-weight: 400; letter-spacing: 2.5px; color: var(--ink-soft); }
  .brand__rule { position: absolute; left: 12px; top: 190px; width: 205px; height: 2px; background: var(--lime); }
  .brand__tagline { position: absolute; left: 12px; top: 203px; width: 205px; text-align: center; font-size: 12px; color: var(--ink-soft); }

  .divider { position: absolute; left: 237px; top: 66px; width: 1px; height: 142px; background: var(--divider); }

  .person { position: absolute; left: 250px; top: 63px; }
  .person__name { font-size: 18px; font-weight: 400; color: var(--lime); line-height: 1.1; }
  .person__title { font-size: 12px; color: var(--ink); margin-top: 2px; }
  .person__address { margin-top: 14px; font-size: 11px; line-height: 14px; color: var(--ghost); }

  .contact { position: absolute; left: 250px; top: 155px; list-style: none; }
  .contact li { display: flex; align-items: center; height: 16.5px; font-size: 12px; }
  .contact svg { width: 9px; height: 9px; margin-right: 7px; fill: var(--lime); }

  .back__name { position: absolute; left: 0; top: 58px; width: 100%; text-align: center; font-size: 34px; letter-spacing: 4px; color: var(--lime-faint); }
  .back__rule { position: absolute; left: 2px; right: 2px; top: 153px; height: 5px; border-radius: 3px; background: var(--lime); }
  .back__line { position: absolute; left: 0; width: 100%; text-align: center; font-size: 19px; }
  .back__line--one { top: 184px; }
  .back__line--two { top: 228px; }
</style>
</head>
<body>
  <section class="card card--front">
    <div class="brand"><span class="brand__mark"></span><span class="brand__name">lumavento</span></div>
    <div class="brand__rule"></div>
    <p class="brand__tagline">Medier til unge</p>

    <div class="divider"></div>

    <div class="person">
      <p class="person__name">Sigrid Holmgaard</p>
      <p class="person__title">Salgsdirektør</p>
      <p class="person__address">Ny Kongensgade 12, 2. sal<br>1472 København K</p>
    </div>

    <ul class="contact">
      <li><svg viewBox="0 0 10 10"><path d="M2 0.5 L3.6 2.6 L2.8 3.6 Q4 6 6.4 7.2 L7.4 6.4 L9.5 8 L8.4 9.5 Q4.5 9.5 0.5 1.6 Z"/></svg>+45 41 27 63 08</li>
      <li><svg viewBox="0 0 10 10"><path d="M0.5 2 H9.5 V8 H0.5 Z M0.8 2.3 L5 5.5 L9.2 2.3" stroke="#f7fafa" stroke-width="0.8"/></svg>sh@lumavento.dk</li>
      <li><svg viewBox="0 0 10 10"><path d="M4 6 L6 4 M3.5 4.5 L2 6 A1.6 1.6 0 0 0 4 8 L5.5 6.5 M6.5 5.5 L8 4 A1.6 1.6 0 0 0 6 2 L4.5 3.5" fill="none" stroke="#a3c73a" stroke-width="1.2"/></svg>www.lumavento.dk</li>
    </ul>
  </section>

  <section class="card card--back">
    <p class="back__name">lumavento</p>
    <div class="back__rule"></div>
    <p class="back__line back__line--one">Lærkevej 14 - 8000</p>
    <p class="back__line back__line--two">Aarhus -Tlf. 86 12 47 30</p>
  </section>
</body>
</html>
```